ultra-minimalist business card

front (black background, matte):

reza t. kovin
writer | photographer
get@rezakovin.com

back (white background, matte):

a picture speaks a thousand words;
a word draws a thousand pictures.

www.rezakovin.com

all text should be small (white or silver - as long as it shows against the black - on the front; black or gray - as long as it shows against the white - on the back).

feel free to get creative in terms of arrangement, alignment, and font type, but remember, the overall style is minimalist, so nothing too fancy, please.

thanks.

```html
<!DOCTYPE html>
<html lang="en">
<head>
<meta charset="utf-8">
<title>Reza T. Kovin — Business Card</title>
<link href="https://fonts.googleapis.com/css2?family=Arimo:wght@400&display=swap" rel="stylesheet">
<style>
  :root {
    --backdrop: #25262b;
    --card-front: #0b0b0b;
    --card-back: #ffffff;
    --ink-light: #e6e6e6;
    --ink-light-muted: #c9c9c9;
    --ink-dark: #111111;
    --card-shadow: rgba(0, 0, 0, 0.45);
  }

  * { box-sizing: border-box; margin: 0; padding: 0; }

  html, body {
    width: 1200px;
    height: 900px;
    overflow: hidden;
  }

  body {
    background: var(--backdrop);
    font-family: "Arimo", Arial, sans-serif;
    display: flex;
    flex-direction: column;
    align-items: center;
    justify-content: center;
    gap: 60px;
  }

  .card {
    width: 600px;
    height: 343px;
    position: relative;
    box-shadow: 0 14px 30px var(--card-shadow);
  }

  /* Front side */
  .card--front {
    background: var(--card-front);
    color: var(--ink-light);
  }

  .identity {
    position: absolute;
    right: 44px;
    bottom: 44px;
    width: 220px;
  }

  .identity__name {
    font-size: 19px;
    font-weight: 400;
    letter-spacing: 0.2px;
    line-height: 1.15;
  }

  .identity__role {
    font-size: 12.5px;
    color: var(--ink-light-muted);
    margin-top: 3px;
  }

  .identity__email {
    font-size: 14px;
    margin-top: 16px;
    letter-spacing: 0.2px;
  }

  /* Back side */
  .card--back {
    background: var(--card-back);
    color: var(--ink-dark);
    display: flex;
    flex-direction: column;
    align-items: center;
    justify-content: center;
  }

  .motto {
    font-size: 19px;
    line-height: 1.3;
    text-align: center;
    letter-spacing: 0.1px;
    margin-top: 10px;
  }

  .website {
    font-size: 16px;
    margin-top: 36px;
    margin-left: 110px;
    letter-spacing: 0.2px;
  }
</style>
</head>
<body>
  <section class="card card--front" aria-label="Card front">
    <div class="identity">
      <p class="identity__name">Reza T. kovin</p>
      <p class="identity__role">writer | photographer</p>
      <p class="identity__email">E: get@rezakovin.com</p>
    </div>
  </section>

  <section class="card card--back" aria-label="Card back">
    <p class="motto">a picture speaks a thousand words.<br>a word draws a thousand pictures.</p>
    <p class="website">www.rezakovin.com</p>
  </section>
</body>
</html>
```